Brand Identity Stationary Package

Hello I'm looking for a full branding package for my Property Management Company. I have a logo but looking to have the following
Business Card
Email signature
Facebook cover photo
Letterhead (word.doc)
#10 Envelope
Pocket Folder - link to 9x12 pocket folder design specs https://www.printorbit-example.ca/marketing-materials/presentation-folders
would like everything to match and be brand identifiable. The company looks after residential properties/apartments and some commercial properties. Attached is a zip of the files.
For Business Card
Name: Gareth Lindqvist
Position: Operations Manager
Number: 1 (555) 384-2917
Email: Gareth@harborkey-example.ca
Website: Harborkey-example.ca
Property Management

```html
<!DOCTYPE html>
<html lang="en">
<head>
<meta charset="utf-8">
<title>Harborkey Envelope Set</title>
<link rel="stylesheet" href="https://fonts.googleapis.com/css2?family=Montserrat:wght@600&family=Source+Sans+3:wght@400&display=swap">
<style>
  :root {
    --backdrop: #d0cfcf;
    --paper: #ffffff;
    --paper-edge: #efeeee;
    --brand-green: #80a642;
    --ink: #111111;
  }
  * { box-sizing: border-box; margin: 0; padding: 0; }
  html, body {
    width: 1200px;
    height: 1050px;
    overflow: hidden;
    background: var(--backdrop);
  }
  .canvas {
    position: relative;
    width: 1200px;
    height: 1050px;
  }
  .envelope {
    position: absolute;
    left: 145px;
    width: 910px;
    height: 390px;
    background: radial-gradient(ellipse at 50% 80%, var(--paper) 0%, var(--paper) 25%, var(--paper-edge) 100%);
    overflow: hidden;
  }
  .envelope--back { top: 105px; }
  .envelope--front { top: 555px; }
  .envelope__art {
    position: absolute;
    inset: 0;
    width: 910px;
    height: 390px;
  }
  .brand-name {
    position: absolute;
    font-family: "Montserrat", sans-serif;
    font-weight: 600;
    font-size: 44px;
    line-height: 1;
    letter-spacing: 6px;
  }
  .envelope--back .brand-name {
    top: 30px;
    left: 0;
    right: 0;
    text-align: center;
    color: var(--paper);
  }
  .envelope--front .brand-name {
    top: 62px;
    left: 52px;
    color: var(--ink);
  }
  .contact-list {
    position: absolute;
    top: 146px;
    left: 52px;
    list-style: none;
    font-family: "Source Sans 3", sans-serif;
    font-size: 20px;
    color: var(--ink);
  }
  .contact-list li {
    display: flex;
    align-items: center;
    height: 26px;
  }
  .contact-icon {
    width: 16px;
    height: 16px;
    margin-right: 13px;
    fill: var(--brand-green);
  }
</style>
</head>
<body>
<main class="canvas">
  <section class="envelope envelope--back" aria-label="Envelope back">
    <svg class="envelope__art" viewBox="0 0 910 390" aria-hidden="true">
      <path d="M0 0 H910 L885 90 Q870 131 820 131 H90 Q40 131 25 90 Z" fill="var(--brand-green)"/>
    </svg>
    <div class="brand-name">HARBORKEY</div>
  </section>

  <section class="envelope envelope--front" aria-label="Envelope front">
    <svg class="envelope__art" viewBox="0 0 910 390" aria-hidden="true">
      <path d="M0 336 C300 356 650 338 910 256 V390 H0 Z" fill="var(--brand-green)"/>
      <path d="M312 336 C550 326 760 290 910 223 V247 C760 294 550 330 312 336 Z" fill="var(--ink)"/>
    </svg>
    <div class="brand-name">HARBORKEY</div>
    <ul class="contact-list">
      <li>
        <svg class="contact-icon" viewBox="0 0 16 16" aria-hidden="true"><path d="M1 6 Q8 1 15 6 L13 8 L11 6.5 V5.5 H5 V6.5 L3 8 Z M4 8 H12 L13 14 H3 Z"/></svg>
        1 (555) 384-2917
      </li>
      <li>
        <svg class="contact-icon" viewBox="0 0 16 16" aria-hidden="true"><path d="M1 3 H15 L8 9 Z M1 4.5 L8 10.5 L15 4.5 V13 H1 Z"/></svg>
        Gareth@harborkey-example.ca
      </li>
      <li>
        <svg class="contact-icon" viewBox="0 0 16 16" aria-hidden="true"><circle cx="8" cy="8" r="7.5"/><path d="M4 4 Q7 5 6 8 Q4 9 3.5 7 Z M10 9 Q12 10 11 13 Q9 12 10 9 Z" fill="var(--paper)"/></svg>
        www.Harborkey-example.ca
      </li>
    </ul>
  </section>
</main>
</body>
</html>
```